Handmade candle business in melbourne requiring assistance with designing classy labels

My business name is Wick and Willow.
I specialise in making handmade candles, i'm based in Melbourne.
My moto is "Delicately hand poured and infused by me...for you"
wickwillow@lanterbox.com
0427 816 093

I need some assistance with designing my labels for my glass candles
I really like earthy colours and nothing too bright, but I want it to look classy and elegant and something that stands out from other homemade candle businesses.
I have attached a sample of a design that appeals to me but open to suggestions.

```html
<!DOCTYPE html>
<html lang="en">
<head>
<meta charset="utf-8">
<title>Wick and Willow – Candle Label</title>
<link rel="stylesheet" href="https://fonts.googleapis.com/css2?family=Pinyon+Script&family=Open+Sans:wght@700&display=swap">
<style>
  :root {
    --page: #ffffff;
    --gold: #c6a651;
    --gold-soft: #cbbb62;
    --sage: #cce07a;
    --ink: #111111;
    --contact-grey: #655c5c;
  }
  html, body {
    margin: 0;
    padding: 0;
    width: 1200px;
    height: 984px;
    overflow: hidden;
    background: var(--page);
  }
  .label {
    display: block;
    width: 1200px;
    height: 984px;
  }
  .label__bg-top { stop-color: var(--gold); }
  .label__bg-upper { stop-color: var(--gold-soft); }
  .label__bg-mid { stop-color: var(--sage); }
  .motto {
    font-family: "Pinyon Script", cursive;
    fill: var(--ink);
  }
  .motto--lead { font-size: 152px; }
  .motto--line { font-size: 96px; }
  .email {
    font-family: "Open Sans", Arial, sans-serif;
    font-weight: 700;
    font-size: 46px;
    fill: var(--contact-grey);
  }
  .phone {
    font-family: "Open Sans", Arial, sans-serif;
    font-weight: 700;
    font-size: 54px;
    fill: var(--ink);
  }
</style>
</head>
<body>
<svg class="label" viewBox="0 0 1200 984" xmlns="http://www.w3.org/2000/svg" aria-label="Wick and Willow candle label">
  <defs>
    <linearGradient id="label-fill" x1="0" y1="0" x2="0" y2="1">
      <stop offset="0" class="label__bg-top"/>
      <stop offset="0.25" class="label__bg-upper"/>
      <stop offset="0.5" class="label__bg-mid"/>
      <stop offset="0.75" class="label__bg-upper"/>
      <stop offset="1" class="label__bg-top"/>
    </linearGradient>
  </defs>

  <path class="label__shape" fill="url(#label-fill)"
        transform="scale(1.1846 1.1841)"
        d="M540 2 C740 0 860 170 960 330 C1030 450 1030 590 950 690
           C850 790 660 830 505 830 C330 830 130 785 45 690
           C-10 610 -5 470 85 345 C220 160 350 4 540 2 Z"/>

  <text class="motto motto--lead" x="598" y="268" text-anchor="middle">Delicately</text>
  <text class="motto motto--line" x="607" y="441" text-anchor="middle">hand poured and infused</text>
  <text class="motto motto--line" x="600" y="557" text-anchor="middle">by me...for you</text>

  <text class="email" x="610" y="740" text-anchor="middle">wickwillow@lanterbox.com</text>

  <text class="phone" x="626" y="861" text-anchor="middle">0427 816 093</text>
</svg>
</body>
</html>
```